School Poster

Design so that these can be placed in classrooms across the school.

Attached is another design we have had done. Use a similar theme.

Consider using themes from https://corvalhs.edq.example.au/

please edit Binder1 doc.

Students and teachers

```html
<!DOCTYPE html>
<html lang="en">
<head>
<meta charset="utf-8">
<title>Classroom Posters – Corval State High School</title>
<link href="https://fonts.googleapis.com/css2?family=Poppins:wght@300;400;500;600;700;800&display=swap" rel="stylesheet">
<style>
  :root {
    --navy: #2f4a98;
    --navy-dark: #233a80;
    --yellow: #f2dc3c;
    --page-bg: #e7e8e7;
    --white: #ffffff;
    --ink: #2b2b2b;
    --soft-blue: #e6eefb;
    --soft-yellow: #fef9e4;
    --yellow-line: #f5e9b4;
    --red: #cf2a2a;
  }
  * { box-sizing: border-box; margin: 0; padding: 0; }
  html, body { width: 1200px; height: 960px; overflow: hidden; }
  body {
    background: var(--page-bg);
    font-family: "Poppins", sans-serif;
    color: var(--ink);
    position: relative;
  }
  .poster {
    position: absolute;
    top: 144px;
    width: 476px;
    height: 672px;
    background: var(--white);
    overflow: hidden;
  }
  .poster--help { left: 106px; }
  .poster--ai {
    left: 618px;
    background: linear-gradient(180deg, #e4ecfb 0%, #f3f6fd 45%, #ffffff 70%);
  }
  .abs { position: absolute; }

  /* header */
  .header-band {
    position: absolute; left: 0; top: 34px; width: 100%; height: 34px;
    background: var(--navy);
  }
  .header-title {
    position: absolute; top: 34px; height: 34px; line-height: 35px;
    color: var(--white); font-weight: 800; white-space: nowrap;
  }
  .poster--help .header-title { left: 95px; font-size: 21.5px; letter-spacing: -0.2px; }
  .poster--ai .header-title { left: 94px; font-size: 16.6px; letter-spacing: -0.1px; }
  .header-title .accent { color: var(--yellow); }
  .school-badge {
    position: absolute; left: 25px; top: 20px; width: 54px; height: 62px;
    background: var(--white);
    display: flex; align-items: center; justify-content: center; text-align: center;
    color: var(--navy); font-weight: 800; font-size: 10px; line-height: 12px;
    box-shadow: 0 1px 3px rgba(0,0,0,.2);
  }

  /* pills */
  .pill {
    position: absolute; height: 26px; border-radius: 13px;
    display: flex; align-items: center; justify-content: center;
    white-space: nowrap;
  }
  .pill--navy { background: var(--navy); color: var(--white); }
  .pill--yellow { background: var(--yellow); color: var(--navy); }
  .pill--steps { left: 130px; top: 80px; width: 215px; font-size: 16.5px; font-weight: 400; }
  .pill--section { font-size: 16.5px; font-weight: 800; }

  /* step cards */
  .step-card {
    position: absolute; left: 40px; width: 412px;
    border: 1.2px solid var(--navy); border-radius: 6px;
  }
  .step-number {
    position: absolute; left: 31px; width: 25px; height: 25px; border-radius: 50%;
    background: var(--navy); color: var(--yellow); font-weight: 800; font-size: 17px;
    display: flex; align-items: center; justify-content: center;
    box-shadow: 0 0 0 3px var(--white);
  }
  .step-icon { position: absolute; border-radius: 8px; }
  .step-label {
    position: absolute; left: 48px; width: 110px; text-align: center;
    color: var(--navy); font-weight: 800; line-height: 0.95; letter-spacing: -0.3px;
  }
  .step-body { position: absolute; left: 178px; width: 270px; }
  .step-heading { font-size: 13.7px; font-weight: 700; line-height: 19px; color: var(--ink); }
  .step-list { list-style: none; font-size: 13.6px; font-weight: 400; line-height: 19px; }
  .step-list li { position: relative; padding-left: 20px; }
  .step-list li::before {
    content: ""; position: absolute; left: 2px; top: 7px; width: 6px; height: 6px;
    border-radius: 50%; background: var(--ink);
  }
  .step-list li.blue::before { background: var(--navy); }

  .motto {
    position: absolute; top: 596px; width: 110px; height: 26px; border-radius: 13px;
    background: var(--navy); color: var(--white); font-weight: 800; font-size: 13px;
    display: flex; align-items: center; justify-content: center; letter-spacing: 0.2px;
  }
  .motto span { color: var(--yellow); margin-left: 4px; }

  /* footer */
  .footer-wave { position: absolute; left: 0; top: 626px; overflow: visible; }
  .references {
    position: absolute; left: 0; top: 636px; width: 100%; text-align: center;
    color: var(--white); font-size: 4.2px; line-height: 6px;
  }
  .references strong { font-weight: 700; }
  .footer-line {
    position: absolute; left: 0; top: 642px; width: 100%; text-align: center;
    color: var(--white); font-size: 11.6px; font-weight: 700;
  }

  /* AI poster */
  .must-list { position: absolute; list-style: none; font-size: 11.7px; font-weight: 700; line-height: 14px; color: var(--ink); }
  .must-list li { position: relative; padding-left: 15px; margin-bottom: 4.5px; }
  .must-list li svg { position: absolute; left: 0; top: 3px; }
  .ai-graphic {
    position: absolute; left: 348px; top: 117px; width: 102px; height: 106px;
    border-radius: 10px; background: linear-gradient(135deg, #dbe4f7, #f3ecc0);
  }
  .help-box {
    position: absolute; left: 24px; top: 241px; width: 427px; height: 208px;
    background: var(--soft-yellow); border: 1px solid var(--yellow-line); border-radius: 8px;
  }
  .help-note {
    position: absolute; left: 0; top: 280px; width: 100%; text-align: center;
    color: var(--navy); font-size: 12.6px; font-weight: 400;
  }
  .help-divider { position: absolute; top: 318px; width: 1px; height: 120px; background: #9aa5c8; }
  .help-item { position: absolute; top: 310px; width: 100px; text-align: center; }
  .help-icon { width: 58px; height: 62px; margin: 0 auto; border-radius: 8px; background: linear-gradient(135deg, #c9d4ee, #f2e6a6); }
  .help-label { margin-top: 22px; font-size: 11.4px; font-weight: 700; line-height: 13px; color: var(--ink); }

  .no-card {
    position: absolute; top: 505px; width: 101px; height: 112px;
    background: var(--soft-blue); border: 1px solid var(--navy); border-radius: 6px;
    text-align: center;
  }
  .no-card svg { display: block; margin: 6px auto 0; }
  .no-card p { margin-top: 6px; font-size: 10.4px; font-weight: 700; line-height: 11.6px; color: var(--ink); }
</style>
</head>
<body>

<!-- Help-seeking poster -->
<section class="poster poster--help">
  <div class="header-band"></div>
  <div class="school-badge">CORVAL<br>SHS</div>
  <h1 class="header-title">BEFORE YOU ASK <span class="accent">THE TEACHER...</span></h1>

  <div class="pill pill--navy pill--steps">TRY THESE STEPS FIRST!</div>

  <!-- Step 1 -->
  <div class="step-card" style="top:123px;height:108px;"></div>
  <div class="step-number" style="top:111px;">1</div>
  <div class="step-icon" role="img" aria-label="Head outline with a glowing lightbulb idea" style="left:75px;top:129px;width:58px;height:55px;background:linear-gradient(135deg,#d3dcf1,#f6e89a);"></div>
  <div class="step-label" style="top:190px;font-size:20px;">THINK<br>FIRST</div>
  <div class="step-body" style="top:130px;">
    <p class="step-heading">Don't give up straight away</p>
    <ul class="step-list">
      <li>Read the question carefully.</li>
      <li class="blue">Identify what you already know.</li>
      <li>Try a strategy you've used before.</li>
      <li class="blue">Give yourself thinking time.</li>
    </ul>
  </div>

  <!-- Step 2 -->
  <div class="step-card" style="top:250px;height:150px;"></div>
  <div class="step-number" style="top:242px;">2</div>
  <div class="step-icon" role="img" aria-label="Clipboard checklist with ticks" style="left:80px;top:276px;width:46px;height:56px;background:linear-gradient(135deg,#d3dcf1,#f6e89a);"></div>
  <div class="step-label" style="top:342px;font-size:16.5px;left:42px;width:122px;">CHECK YOUR<br>SUPPORTS</div>
  <div class="step-body" style="top:259px;">
    <p class="step-heading">Before asking for help, check:</p>
    <ul class="step-list">
      <li>Learning goal and success criteria.</li>
      <li>Worked examples.</li>
      <li>Class notes.</li>
      <li>Classroom displays.</li>
      <li>Learnhub resources.</li>
      <li>Task sheet and instructions.</li>
    </ul>
  </div>

  <!-- Step 3 -->
  <div class="step-card" style="top:418px;height:170px;"></div>
  <div class="step-number" style="top:409px;">3</div>
  <div class="step-icon" role="img" aria-label="Three people with speech bubbles" style="left:63px;top:454px;width:78px;height:57px;background:linear-gradient(135deg,#f6e89a,#c3cfee);"></div>
  <div class="step-label" style="top:520px;font-size:17px;">ASK 3<br>BEFORE ME</div>
  <div class="step-body" style="top:425px;">
    <p class="step-heading">Ask three sources before asking the teacher</p>
    <ul class="step-list">
      <li>A person (partner or neighbour)</li>
      <li>A place (notes, display, Learnhub)</li>
      <li>A resource (worked example, task sheet)</li>
    </ul>
    <p class="step-heading">Then ask the teacher if you still need help.</p>
  </div>

  <div class="motto" style="left:40px;">WE<span>BELIEVE</span></div>
  <div class="motto" style="left:190px;">WE<span>STRIVE</span></div>
  <div class="motto" style="left:341px;">WE<span>ACHIEVE</span></div>

  <svg class="footer-wave" width="476" height="46" viewBox="0 0 476 46">
    <path d="M0 16 Q238 -16 476 16 L476 46 L0 46 Z" fill="var(--navy)"/>
  </svg>
  <p class="references">
    <strong>References</strong><br>
    Holloway, R. (2025). Why Students Hold Back from Asking for Help – And How to Shift It. Downloaded 24/04/2026 from: https://www.learnwell.example.org/article/asking-for-help/<br>
    Evidence Learning Institute (2024). Supporting Self-Regulated Learning. Downloaded 24/04/2026 from: https://www.evidencelearning.example.au/files/self-regulated-learning.pdf
  </p>
</section>

<!-- Responsible AI poster -->
<section class="poster poster--ai">
  <div class="header-band"></div>
  <div class="school-badge">CORVAL<br>SHS</div>
  <h1 class="header-title">USING AI AND OTHER TOOLS RESPONSIBLY</h1>

  <div class="pill pill--navy pill--section" style="left:118px;top:80px;width:239px;">WHAT YOU MUST DO:</div>

  <ul class="must-list" style="left:32px;top:131px;width:180px;">
    <li><svg width="8" height="8" viewBox="0 0 8 8"><rect x="0.5" y="0.5" width="7" height="7" fill="none" stroke="var(--navy)"/><path d="M1.8 4 L3.4 5.6 L6.3 2.2" fill="none" stroke="var(--navy)" stroke-width="1"/></svg>Complete your own work</li>
    <li><svg width="8" height="8" viewBox="0 0 8 8"><rect x="0.5" y="0.5" width="7" height="7" fill="none" stroke="var(--navy)"/><path d="M1.8 4 L3.4 5.6 L6.3 2.2" fill="none" stroke="var(--navy)" stroke-width="1"/></svg>Demonstrate your progress (drafts, notes, planning, revisions)</li>
    <li><svg width="8" height="8" viewBox="0 0 8 8"><rect x="0.5" y="0.5" width="7" height="7" fill="none" stroke="var(--navy)"/><path d="M1.8 4 L3.4 5.6 L6.3 2.2" fill="none" stroke="var(--navy)" stroke-width="1"/></svg>Use feedback to improve your work</li>
  </ul>
  <ul class="must-list" style="left:218px;top:131px;width:128px;">
    <li><svg width="8" height="8" viewBox="0 0 8 8"><rect x="0.5" y="0.5" width="7" height="7" fill="none" stroke="var(--navy)"/><path d="M1.8 4 L3.4 5.6 L6.3 2.2" fill="none" stroke="var(--navy)" stroke-width="1"/></svg>Demonstrate your understanding of the ideas in your submission</li>
  </ul>
  <div class="ai-graphic" role="img" aria-label="Brain outline joined to an AI chip with circuit lines"></div>

  <div class="help-box"></div>
  <div class="pill pill--yellow pill--section" style="left:109px;top:250px;width:256px;height:25px;">WHAT AI CAN HELP YOU DO</div>
  <p class="help-note">(when approved by your teacher)</p>

  <div class="help-divider" style="left:131px;"></div>
  <div class="help-divider" style="left:238px;"></div>
  <div class="help-divider" style="left:345px;"></div>

  <div class="help-item" style="left:28px;">
    <div class="help-icon" role="img" aria-label="Brain with sparks"></div>
    <p class="help-label">Brainstorm ideas</p>
  </div>
  <div class="help-item" style="left:135px;">
    <div class="help-icon" role="img" aria-label="Checklist with magnifying glass"></div>
    <p class="help-label">Check spelling, grammar and clarity</p>
  </div>
  <div class="help-item" style="left:242px;">
    <div class="help-icon" role="img" aria-label="Phone reading text aloud"></div>
    <p class="help-label">Read your work aloud using text-to-speech tools</p>
  </div>
  <div class="help-item" style="left:348px;">
    <div class="help-icon" role="img" aria-label="Rising bar chart with arrow and gear"></div>
    <p class="help-label">Help identify areas for improvement in a draft</p>
  </div>

  <div class="pill pill--navy pill--section" style="left:109px;top:472px;width:256px;height:25px;">WHAT YOU CANNOT DO:</div>

  <div class="no-card" style="left:24px;">
    <svg width="30" height="30" viewBox="0 0 30 30"><circle cx="15" cy="15" r="12" fill="none" stroke="var(--red)" stroke-width="3"/><path d="M10 10 L20 20 M20 10 L10 20" stroke="var(--red)" stroke-width="3" stroke-linecap="round"/></svg>
    <p>Submit AI-generated work as your own</p>
  </div>
  <div class="no-card" style="left:133px;">
    <svg width="30" height="30" viewBox="0 0 30 30"><circle cx="15" cy="15" r="12" fill="none" stroke="var(--red)" stroke-width="3"/><path d="M10 10 L20 20 M20 10 L10 20" stroke="var(--red)" stroke-width="3" stroke-linecap="round"/></svg>
    <p>Copy and paste AI responses without acknowledging or adapting them</p>
  </div>
  <div class="no-card" style="left:242px;">
    <svg width="30" height="30" viewBox="0 0 30 30"><circle cx="15" cy="15" r="12" fill="none" stroke="var(--red)" stroke-width="3"/><path d="M10 10 L20 20 M20 10 L10 20" stroke="var(--red)" stroke-width="3" stroke-linecap="round"/></svg>
    <p>Use AI tools to complete the whole task for you</p>
  </div>
  <div class="no-card" style="left:350px;">
    <svg width="30" height="30" viewBox="0 0 30 30"><circle cx="15" cy="15" r="12" fill="none" stroke="var(--red)" stroke-width="3"/><path d="M10 10 L20 20 M20 10 L10 20" stroke="var(--red)" stroke-width="3" stroke-linecap="round"/></svg>
    <p>Submit work that does not demonstrate your understanding</p>
  </div>

  <svg class="footer-wave" width="476" height="46" viewBox="0 0 476 46">
    <path d="M0 16 Q238 -16 476 16 L476 46 L0 46 Z" fill="var(--navy)"/>
  </svg>
  <p class="footer-line">If you didn't create, develop and understand it, it isn't your work.</p>
</section>

</body>
</html>
```